Cognitive therapist.

I am a therapist and my main work is with clients who have depression and anxiety disorders.

I need something reasonably plain. Cognitive therapy is a very pragmatic approach to dealing with problems, so it isn't new agey (no offence to new age therapies at all)
Updates

Hi everyone, I am currently looking at a particular design that I will most likely go with. Cheers, Meg

Industry/Entity Type

Work

Contact Information for Business Card

Meg Tarvish
Cognitive Therapist
BA, PG Dip Mental Health,
PG Dip Cog Beh Therapy
MKTPR

The Quarry Lodge,
Level One
48 Marlow Parade
Cnr Fenwick St & Marlow Parade
P O Box 38 219
KESTONE 5827

Phone: 021 574 3082 Email: mtarvish@quellnet.co.nz

www.megtarvish.co.nz

Requirements
Should not have
• No illustration, or colour. not old style fonts.

```html
<!DOCTYPE html>
<html lang="en">
<head>
<meta charset="utf-8">
<title>Meg Tarvish – Business Card</title>
<link href="https://fonts.googleapis.com/css2?family=Fira+Sans:wght@400;500;600&display=swap" rel="stylesheet">
<style>
  :root {
    --backdrop: #8a5b3b;
    --card-dark: #262626;
    --card-mid: #707070;
    --brand-blue: #00a2d4;
    --swoosh-white: #ffffff;
    --swoosh-grey: #b5b5b5;
    --divider: #1a1a1a;
    --text-light: #ffffff;
    --text-soft: #f0f0f0;
    --icon-tint: #dff3fb;
  }
  html, body {
    margin: 0;
    padding: 0;
    width: 1200px;
    height: 864px;
    overflow: hidden;
    background: var(--backdrop);
    font-family: "Fira Sans", sans-serif;
  }
  .business-card {
    position: absolute;
    left: 155px;
    top: 190px;
    width: 855px;
    height: 488px;
    overflow: hidden;
    color: var(--text-light);
    box-shadow: 4px 5px 6px rgba(0,0,0,0.35);
  }
  .card-artwork {
    position: absolute;
    inset: 0;
    width: 100%;
    height: 100%;
  }
  .divider {
    position: absolute;
    left: 300px;
    top: 67px;
    width: 2px;
    height: 268px;
    background: var(--divider);
    box-shadow: 1px 0 0 rgba(255,255,255,0.08);
  }
  .identity {
    position: absolute;
    left: 327px;
    top: 60px;
  }
  .therapist-name {
    margin: 0;
    font-size: 50px;
    font-weight: 600;
    line-height: 1;
    letter-spacing: 0.3px;
    text-shadow: 0 2px 3px rgba(0,0,0,0.45);
  }
  .qualifications {
    margin: 10px 0 0;
    font-size: 20px;
    font-weight: 400;
    line-height: 33px;
    color: var(--text-soft);
  }
  .address {
    position: absolute;
    left: 327px;
    top: 241px;
    margin: 0;
    font-style: normal;
    font-size: 19.5px;
    line-height: 24.5px;
    color: var(--text-soft);
  }
  .contact-list {
    position: absolute;
    left: 38px;
    top: 410px;
    margin: 0;
    padding: 0;
    list-style: none;
    font-size: 19px;
    font-weight: 500;
  }
  .contact-item {
    display: flex;
    align-items: center;
    height: 30px;
  }
  .contact-icon {
    width: 26px;
    height: 22px;
    margin-right: 15px;
  }
  .website {
    position: absolute;
    right: 46px;
    top: 438px;
    font-size: 23px;
    font-weight: 500;
    letter-spacing: 1px;
    line-height: 30px;
  }
</style>
</head>
<body>
  <main class="business-card">
    <svg class="card-artwork" viewBox="0 0 570 325" preserveAspectRatio="none" aria-hidden="true">
      <defs>
        <radialGradient id="cardGlow" cx="0.5" cy="0.42" r="0.62">
          <stop offset="0" stop-color="var(--card-mid)"/>
          <stop offset="1" stop-color="var(--card-dark)"/>
        </radialGradient>
        <linearGradient id="swooshShade" x1="0" y1="0" x2="1" y2="0">
          <stop offset="0" stop-color="var(--swoosh-white)"/>
          <stop offset="0.55" stop-color="var(--swoosh-grey)"/>
          <stop offset="1" stop-color="var(--swoosh-white)"/>
        </linearGradient>
        <linearGradient id="portraitTone" x1="0" y1="0" x2="0" y2="1">
          <stop offset="0" stop-color="#7a7a7a"/>
          <stop offset="1" stop-color="#4a4a4a"/>
        </linearGradient>
      </defs>
      <rect class="card-base" width="570" height="325" fill="url(#cardGlow)"/>
      <path class="portrait" role="img" aria-label="Portrait photograph of the therapist"
            d="M40,8 L172,8 L176,260 C120,246 74,222 22,190 L22,120 C30,100 36,60 40,8 Z" fill="url(#portraitTone)"/>
      <path class="accent-line" d="M346,0 C440,14 520,52 570,96" fill="none" stroke="var(--swoosh-white)" stroke-width="1.2"/>
      <path class="accent-swoosh" d="M366,0 C452,10 530,45 570,76 L570,54 C545,38 492,14 408,0 Z" fill="url(#swooshShade)"/>
      <path class="accent-blue" d="M408,0 C492,14 545,38 570,54 L570,0 Z" fill="var(--brand-blue)"/>
      <path class="accent-line" d="M0,123 C70,190 150,248 260,276" fill="none" stroke="var(--swoosh-white)" stroke-width="1.2"/>
      <path class="accent-line" d="M0,135 C70,200 150,256 260,280" fill="none" stroke="var(--swoosh-white)" stroke-width="0.8"/>
      <path class="accent-swoosh" d="M0,170 C100,238 210,282 310,278 C430,272 520,248 570,232 L570,240 C520,256 420,286 300,288 C200,292 90,250 0,186 Z" fill="url(#swooshShade)"/>
      <path class="accent-blue" d="M0,186 C90,250 200,292 300,288 C420,286 520,256 570,240 L570,325 L0,325 Z" fill="var(--brand-blue)"/>
    </svg>

    <div class="divider"></div>

    <header class="identity">
      <h1 class="therapist-name">Meg Tarvish</h1>
      <p class="qualifications">Cognitive Therapist BA,<br>PG Dip Mental Health, PG Dip Cog Beh Therapy</p>
    </header>

    <address class="address">
      MKTPR The Quarry Lodge, Level<br>
      One 48 Marlow Parade Cnr Fenwick St<br>
      &amp; Marlow Parade P O Box 38 219<br>
      KESTONE 5827
    </address>

    <ul class="contact-list">
      <li class="contact-item">
        <svg class="contact-icon" viewBox="0 0 34 28" aria-hidden="true">
          <path d="M6,8 C6,4 10,3 17,3 C24,3 28,4 28,8 L24,11 L21,8 L13,8 L10,11 Z" fill="var(--icon-tint)"/>
          <path d="M9,12 L25,12 L29,24 L5,24 Z" fill="var(--icon-tint)"/>
          <circle cx="17" cy="18" r="3.5" fill="var(--brand-blue)"/>
        </svg>
        <span>021 574 3082</span>
      </li>
      <li class="contact-item">
        <svg class="contact-icon" viewBox="0 0 34 28" aria-hidden="true">
          <rect x="4" y="6" width="26" height="18" rx="2" fill="var(--icon-tint)"/>
          <path d="M4,8 L17,17 L30,8" fill="none" stroke="var(--brand-blue)" stroke-width="2"/>
        </svg>
        <span>mtarvish@quellnet.co.nz</span>
      </li>
    </ul>

    <div class="website">www.megtarvish.co.nz</div>
  </main>
</body>
</html>
```